Vellmore Family Law, legal technician needs a website and design

I need a website for a family law practice. I specialize in collaborative law, unbundled services, and mediation. The website must contain my company logo (file attached), and the website must be a mixture of my personality and my profession. I have attached additional information to explain my personality and profession.

Target Market(s)

Lower through middle-class (income level up to $200,000 per year)

Coding

Coded - Design and coding required

Number of Pages Required

1 page

Requirements
Must have
• Must have enough pages to cover required content. I submitted below some content about the collaborative law process. All of the content is not necessary. However, the website must have enough content to clearly describe the services I offer. Use your professionalism and judgment regarding font, font size, etc.

```html
<!DOCTYPE html>
<html lang="en">
<head>
<meta charset="utf-8">
<title>Vellmore Family Law</title>
<link href="https://fonts.googleapis.com/css2?family=Rubik:wght@500;700&family=Roboto:wght@400;500;700&display=swap" rel="stylesheet">
<style>
:root{
  --navy:#03052e;
  --lime:#bcc23a;
  --lime-deep:#a8b02c;
  --ink:#1a1a2a;
  --muted:#666a74;
  --white:#ffffff;
  --footer:#1d1d1d;
  --field:#f3f3f3;
}
*{box-sizing:border-box;margin:0;padding:0}
html,body{width:1200px;height:4195px;overflow:hidden}
body{font-family:"Roboto",Arial,sans-serif;color:var(--ink);background:var(--white)}
.page{position:relative;width:1200px;height:4195px;overflow:hidden}
.abs{position:absolute}
h1,h2,h3{font-family:"Rubik",Arial,sans-serif;font-weight:700}
.btn{position:absolute;display:flex;align-items:center;justify-content:center;gap:6px;font-family:"Roboto",sans-serif;font-weight:700;font-size:14px;text-transform:uppercase;border:2px solid}
.btn svg{width:13px;height:13px}

/* hero */
.hero{left:0;top:0;width:1200px;height:599px;background:linear-gradient(180deg,#1a1530 0%,#2b2236 40%,#4a3328 75%,#6a4a30 100%)}
.brand{left:111px;top:16px;display:flex;align-items:center;gap:14px}
.brand-mark{width:58px;height:58px;background:var(--lime);flex:none}
.brand-name{font-family:"Roboto",sans-serif;font-weight:500;font-size:26px;color:var(--lime);line-height:1.05;width:170px}
.call{left:862px;top:28px;display:flex;align-items:center;gap:12px;color:var(--white)}
.call-ring{width:40px;height:40px;border:2px solid var(--lime);border-radius:50%;display:flex;align-items:center;justify-content:center;flex:none}
.call small{display:block;font-size:14px}
.call strong{font-size:21px;font-weight:700}
.nav{right:111px;top:94px;display:flex;gap:33px;list-style:none}
.nav li{font-size:14px;font-weight:700;color:var(--white)}
.nav li.active{color:var(--lime)}
.hero-title{left:0;width:1200px;top:258px;text-align:center;color:var(--white);font-size:50px;letter-spacing:.5px}
.hero .btn{left:524px;top:330px;width:152px;height:45px;color:var(--white);border-color:var(--white)}
.slide-arrow{width:38px;height:38px;border-radius:50%;background:rgba(255,255,255,.8);display:flex;align-items:center;justify-content:center;top:324px}

/* services */
.card{top:707px;width:315px;height:281px;background:var(--navy);color:var(--white);text-align:center}
.card-inner{position:absolute;inset:16px;border:2px solid var(--white);padding-top:20px}
.card-icon{width:93px;height:93px;border-radius:50%;background:var(--lime);margin:0 auto 24px;display:flex;align-items:center;justify-content:center}
.card h3{font-family:"Roboto",sans-serif;font-size:16px;margin-bottom:14px}
.card p{font-size:13px;line-height:22px;padding:0 20px}

/* about */
.about-photo{left:111px;top:1092px;width:472px;height:422px;border:4px solid var(--navy);background:linear-gradient(135deg,#3a4a5e 0%,#c9b49a 50%,#d9cfc2 100%)}
.play{left:330px;top:1285px;width:32px;height:32px;border-radius:50%;background:var(--white)}
.about-title{left:627px;top:1086px;font-size:32px;color:var(--navy)}
.about-text{left:627px;top:1138px;width:462px;font-size:13px;line-height:22.3px;color:var(--muted);text-align:justify}
.about-btn{left:627px;top:1468px;width:153px;height:46px;color:var(--navy);border-color:var(--navy)}

/* testimonial */
.clients-title{left:0;width:1200px;top:1605px;text-align:center;font-size:32px;color:var(--navy)}
.quote-box{left:192px;top:1691px;width:817px;height:264px;background:var(--lime)}
.quote-badge{left:244px;top:1664px;width:62px;height:58px;background:var(--navy);display:flex;align-items:center;justify-content:center;color:var(--white);font-family:"Rubik",sans-serif;font-size:34px}
.quote-text{left:252px;top:1752px;width:697px;text-align:center;font-style:italic;font-size:13px;line-height:22.5px;color:var(--white)}
.quote-rule{left:403px;top:1882px;width:355px;height:1px;background:rgba(255,255,255,.7)}
.quote-name{left:0;width:1200px;top:1897px;text-align:center;font-family:"Rubik",sans-serif;font-weight:700;font-size:21px;color:var(--white)}
.q-arrows{left:880px;top:1884px;width:130px;height:71px;background:var(--white)}
.q-btn{top:1893px;width:56px;height:56px;display:flex;align-items:center;justify-content:center}

/* team */
.team-panel{left:0;top:2059px;width:600px;height:510px;background:var(--navy)}
.team-photo{left:600px;top:2059px;width:600px;height:510px;background:linear-gradient(135deg,#e9eef3 0%,#9aa6b4 45%,#5b6674 100%)}
.team-title{left:111px;top:2126px;font-size:32px;color:var(--white)}
.team-text{left:111px;top:2180px;width:450px;font-size:13px;line-height:22.3px;color:var(--white)}
.team-btn{left:111px;top:2444px;width:155px;height:46px;color:var(--white);border-color:var(--white)}

/* blog */
.blog-title{left:0;width:1200px;top:2660px;text-align:center;font-size:32px;color:var(--navy)}
.blog-img{top:2727px;width:475px;height:301px}
.blog-card{top:2943px;width:388px;height:158px;background:var(--white);border-left:6px solid var(--navy);border-bottom:6px solid var(--navy);padding:22px 28px 0 30px}
.blog-card h3{font-size:21px;color:var(--navy);margin-bottom:18px;font-weight:500}
.blog-card p{font-size:13px;line-height:22.3px;color:var(--muted)}
.side-arrow{top:2914px;width:55px;height:55px;background:#c9c9c9;display:flex;align-items:center;justify-content:center}

/* contact */
.contact{left:0;top:3204px;width:1200px;height:606px;background:linear-gradient(180deg,var(--lime) 0%,var(--lime-deep) 100%)}
.contact-title{left:0;width:1200px;top:3296px;text-align:center;font-size:32px;color:var(--white)}
.field{height:57px;width:351px;background:var(--field);border:1px solid #d5d5d5;font-size:13px;color:#888;padding:20px 22px}
.field.msg{height:134px;width:717px}
.submit{left:523px;top:3671px;width:158px;height:48px;border-radius:24px;background:var(--navy);color:var(--white);font-weight:700;font-size:14px;display:flex;align-items:center;justify-content:center}

/* footer */
.site-footer{left:0;top:3810px;width:1200px;height:385px;background:var(--footer)}
.foot-brand{left:236px;top:3886px;display:flex;align-items:center;gap:12px}
.foot-brand .brand-mark{width:52px;height:52px}
.foot-brand .brand-name{font-size:22px;width:140px}
.foot-email{left:466px;top:3885px;width:385px;height:49px;background:var(--white);font-size:13px;color:#888;padding:17px 20px}
.foot-mail{left:856px;top:3885px;width:111px;height:49px;background:var(--lime);color:var(--white);font-weight:700;font-size:12px;display:flex;align-items:center;justify-content:center}
.info{top:3985px;width:300px;height:92px;display:flex;align-items:center;gap:18px;color:var(--white)}
.info-icon{width:92px;height:92px;flex:0 0 92px;border-radius:50%;background:var(--lime);display:flex;align-items:center;justify-content:center}
.info-label{display:block;font-size:13px;font-weight:700;margin-bottom:8px}
.info-value{display:block;font-size:20px;font-weight:700;white-space:nowrap}
.info-value.small{font-size:16px}
.info-address{display:block;font-size:14px;line-height:17px;width:190px}
.foot-rule{left:111px;top:4111px;width:978px;height:1px;background:#3a3a3a}
.copyright{left:0;width:1200px;top:4137px;text-align:center;font-size:14px;font-weight:700;color:var(--white)}
</style>
</head>
<body>
<div class="page">

<header class="hero abs" role="img" aria-label="Night city skyline photograph">
  <div class="brand abs"><span class="brand-mark"></span><span class="brand-name">Vellmore Family Law</span></div>
  <div class="call abs">
    <span class="call-ring"><svg width="18" height="18" viewBox="0 0 24 24"><path fill="#bcc23a" d="M6.6 10.8a15.1 15.1 0 0 0 6.6 6.6l2.2-2.2c.3-.3.7-.4 1-.2 1.1.4 2.3.6 3.6.6.6 0 1 .4 1 1V20c0 .6-.4 1-1 1A17 17 0 0 1 3 4c0-.6.4-1 1-1h3.5c.6 0 1 .4 1 1 0 1.3.2 2.5.6 3.6.1.3 0 .7-.2 1z"/></svg></span>
    <div><small>Free consultation</small><strong>+1 888 888 8888</strong></div>
  </div>
  <ul class="nav abs">
    <li class="active">HOME</li><li>ABOUT US</li><li>SERVICES</li><li>MEDIATION</li><li>BLOG</li><li>CONTACT US</li>
  </ul>
  <h1 class="hero-title abs">VELLMORE FAMILY LAW</h1>
  <div class="btn">Learn more <svg viewBox="0 0 16 16"><circle cx="8" cy="8" r="8" fill="#fff"/><path d="M6 4l4 4-4 4" stroke="#1a1530" stroke-width="2" fill="none"/></svg></div>
  <div class="slide-arrow abs" style="left:74px"><svg width="12" height="12" viewBox="0 0 12 12"><path d="M8 1L3 6l5 5" stroke="#333" stroke-width="1.5" fill="none"/></svg></div>
  <div class="slide-arrow abs" style="left:1088px"><svg width="12" height="12" viewBox="0 0 12 12"><path d="M4 1l5 5-5 5" stroke="#333" stroke-width="1.5" fill="none"/></svg></div>
</header>

<div class="card abs" style="left:111px"><div class="card-inner">
  <div class="card-icon"><svg width="48" height="48" viewBox="0 0 48 48" fill="#03052e"><circle cx="24" cy="24" r="11"/><circle cx="10" cy="14" r="5"/><circle cx="38" cy="14" r="5"/><circle cx="10" cy="34" r="5"/><circle cx="38" cy="34" r="5"/></svg></div>
  <h3>COLLABORATIVE LAW</h3><p>Lorem ipsum dolor sit amet, conse ctetur adipiscing elit, sed do eiusmod tempor incid</p>
</div></div>
<div class="card abs" style="left:443px"><div class="card-inner">
  <div class="card-icon"><svg width="48" height="48" viewBox="0 0 48 48" fill="#03052e"><circle cx="24" cy="10" r="6"/><circle cx="13" cy="22" r="5"/><circle cx="35" cy="22" r="5"/><rect x="6" y="30" width="14" height="12" rx="3"/><rect x="28" y="30" width="14" height="12" rx="3"/><rect x="18" y="18" width="12" height="24" rx="3"/></svg></div>
  <h3>UNBUNDLED SERVICES</h3><p>Lorem ipsum dolor sit amet, conse ctetur adipiscing elit, sed do eiusmod tempor incid</p>
</div></div>
<div class="card abs" style="left:773px"><div class="card-inner">
  <div class="card-icon"><svg width="48" height="48" viewBox="0 0 48 48" fill="#03052e"><circle cx="14" cy="12" r="6"/><circle cx="34" cy="12" r="6"/><path d="M5 42V26a8 8 0 0 1 16 0l3 6 3-6a8 8 0 0 1 16 0v16z"/></svg></div>
  <h3>MEDIATION</h3><p>Lorem ipsum dolor sit amet, conse ctetur adipiscing elit, sed do eiusmod tempor incid</p>
</div></div>

<div class="about-photo abs" role="img" aria-label="Photograph of a client signing a document at a desk"></div>
<div class="play abs"><svg width="32" height="32" viewBox="0 0 32 32"><path d="M13 10l9 6-9 6z" fill="#3a4a5e"/></svg></div>
<h2 class="about-title abs">ABOUT US</h2>
<p class="about-text abs">Lorem ipsum dolor sit amet, consectetur adipiscing elit, sed do eiusmod tempor incididunt ut labore et dolore magna aliqua. Ut enim ad minim veniam, quis nostrud exercitation ullamco laboris nisi ut aliquip ex ea commodo consequat. Duis aute irure dolor in reprehenderit in voluptate velit esse cillum dolore eu fugiat nulla pariatur. Excepteur sint occaecat cupidatat non proident, sunt in culpa qui officia deserunt mollit anim id est laborum. Lorem ipsum dolor sit amet, consectetur adipiscing elit, sed do eiusmod tempor incididunt ut labore et dolore magna aliqua. Ut enim ad minim veniam, quis nostrud exercitation ullamco laboris nisi ut aliquip ex ea commodo consequat. Duis aute irure dolor in reprehenderit in voluptate velit esse cillum dolore eu fugiat nulla pariatur. Excepteur sint occaecat cupidatat non proident, sunt in culpa qui officia deserunt mollit anim id est laborum.</p>
<div class="btn about-btn">Learn more <svg viewBox="0 0 16 16"><circle cx="8" cy="8" r="8" fill="#03052e"/><path d="M6 4l4 4-4 4" stroke="#fff" stroke-width="2" fill="none"/></svg></div>

<h2 class="clients-title abs">WHAT OUR CLIENTS SAY?</h2>
<div class="quote-box abs"></div>
<div class="quote-badge abs">&ldquo;</div>
<p class="quote-text abs">"Lorem ipsum dolor sit amet, consectetur adipiscing elit, sed do eiusmod tempor incididunt ut labore et dolore magna aliqua. Ut enim ad minim veniam, quis nostrud exercitation ullamco laboris nisi ut aliquip ex ea commodo consequat. Duis aute irure dolor in reprehenderit in voluptate velit esse cillum dolore eu fugiat nulla pariatur. Excepteur sint occaecat cupidatat non proident, sunt in culpa qui officia deserunt mollit anim id est laborum."</p>
<div class="quote-rule abs"></div>
<div class="quote-name abs">John Doe</div>
<div class="q-arrows abs"></div>
<div class="q-btn abs" style="left:889px;background:#c9c9c9"><svg width="18" height="16" viewBox="0 0 18 16"><path d="M8 1L1 8l7 7M1 8h16" stroke="#fff" stroke-width="3" fill="none"/></svg></div>
<div class="q-btn abs" style="left:953px;background:var(--navy)"><svg width="18" height="16" viewBox="0 0 18 16"><path d="M10 1l7 7-7 7M17 8H1" stroke="#fff" stroke-width="3" fill="none"/></svg></div>

<div class="team-panel abs"></div>
<div class="team-photo abs" role="img" aria-label="Photograph of a team joining hands over a meeting table"></div>
<h2 class="team-title abs">MEET OUR TEAM</h2>
<p class="team-text abs">Lorem ipsum dolor sit amet, consectetur adipiscing elit, sed do eiusmod tempor incididunt ut labore et dolore magna aliqua. Ut enim ad minim veniam, quis nostrud exercitation ullamco laboris nisi ut aliquip ex ea commodo consequat. Duis aute irure dolor in reprehenderit in voluptate velit esse cillum dolore eu fugiat nulla pariatur. Excepteur sint occaecat cupidatat non proident, sunt in culpa qui officia deserunt mollit anim id est laborum. Lorem ipsum dolor sit amet, consectetur adipiscing elit, sed do eiusmod tempor incididunt ut labore et dolore magna aliqua. Ut enim ad minim veniam, quis nostrud exercitation ullamco laboris nisi ut aliquip ex ea commodo consequat. Duis aute irure dolor in</p>
<div class="btn team-btn">Learn more <svg viewBox="0 0 16 16"><circle cx="8" cy="8" r="8" fill="#fff"/><path d="M6 4l4 4-4 4" stroke="#03052e" stroke-width="2" fill="none"/></svg></div>

<h2 class="blog-title abs">LATEST BLOG</h2>
<div class="blog-img abs" style="left:111px;background:linear-gradient(135deg,#f1ede6 0%,#d9c9b4 55%,#b89a7c 100%)" role="img" aria-label="Photograph of a family relaxing together on a sofa"></div>
<div class="blog-img abs" style="left:614px;background:linear-gradient(180deg,#b9c7d8 0%,#e8c9a4 60%,#f0a866 100%)" role="img" aria-label="Photograph of a parent carrying a child on their shoulders at sunset"></div>
<div class="blog-card abs" style="left:151px"><h3>Lorem ipsum dolor sit amet</h3><p>Lorem ipsum dolor sit amet, consectetur adipisci ng elit, sed do eiusmod tempor incididunt ut labore et dolore magna aliqua.</p></div>
<div class="blog-card abs" style="left:654px"><h3>Lorem ipsum dolor sit amet</h3><p>Lorem ipsum dolor sit amet, consectetur adipisci ng elit, sed do eiusmod tempor incididunt ut labore et dolore magna aliqua.</p></div>
<div class="side-arrow abs" style="left:29px"><svg width="18" height="16" viewBox="0 0 18 16"><path d="M8 1L1 8l7 7M1 8h16" stroke="#fff" stroke-width="3" fill="none"/></svg></div>
<div class="side-arrow abs" style="left:1117px"><svg width="18" height="16" viewBox="0 0 18 16"><path d="M10 1l7 7-7 7M17 8H1" stroke="#fff" stroke-width="3" fill="none"/></svg></div>

<section class="contact abs" role="img" aria-label="Lime-tinted city skyline background"></section>
<h2 class="contact-title abs">CONTACT US</h2>
<div class="field abs" style="left:241px;top:3361px">First name</div>
<div class="field abs" style="left:610px;top:3361px">Last name</div>
<div class="field abs" style="left:241px;top:3436px">Phone</div>
<div class="field abs" style="left:610px;top:3436px">Email address</div>
<div class="field msg abs" style="left:241px;top:3514px">Message</div>
<div class="submit abs">SUBMIT</div>

<footer class="site-footer abs"></footer>
<div class="foot-brand abs"><span class="brand-mark"></span><span class="brand-name">Vellmore Family Law</span></div>
<div class="foot-email abs">Email us</div>
<div class="foot-mail abs">MAIL US</div>
<div class="info abs" style="left:111px">
  <div class="info-icon"><svg width="32" height="32" viewBox="0 0 24 24"><path fill="#1d1d1d" d="M6.6 10.8a15.1 15.1 0 0 0 6.6 6.6l2.2-2.2c.3-.3.7-.4 1-.2 1.1.4 2.3.6 3.6.6.6 0 1 .4 1 1V20c0 .6-.4 1-1 1A17 17 0 0 1 3 4c0-.6.4-1 1-1h3.5c.6 0 1 .4 1 1 0 1.3.2 2.5.6 3.6.1.3 0 .7-.2 1z"/></svg></div>
  <div><span class="info-label">Call us Today :</span><span class="info-value">+1 888 888 8888</span></div>
</div>
<div class="info abs" style="left:464px">
  <div class="info-icon"><svg width="34" height="26" viewBox="0 0 34 26"><rect x="1" y="1" width="32" height="24" rx="2" fill="#1d1d1d"/><path d="M2 3l15 11L32 3" stroke="#bcc23a" stroke-width="2.5" fill="none"/></svg></div>
  <div><span class="info-label">Mail us Today :</span><span class="info-value small">info@companyname.com</span></div>
</div>
<div class="info abs" style="left:817px">
  <div class="info-icon"><svg width="24" height="32" viewBox="0 0 24 32"><path d="M12 1a11 11 0 0 1 11 11c0 8-11 19-11 19S1 20 1 12A11 11 0 0 1 12 1z" fill="#1d1d1d"/><circle cx="12" cy="12" r="4" fill="#bcc23a"/></svg></div>
  <div><span class="info-label">Address :</span><span class="info-address">Lorem ipsum dolor sit amet consectetur adipiscing</span></div>
</div>
<div class="foot-rule abs"></div>
<p class="copyright abs">© Copyrights 2021 Company name | All Rights Reserved</p>

</div>
</body>
</html>
```